Business Card Design To Look Just Like a Credit Card- Needed

I would like to take my new Logo just designed here at Artisan Hive and make a new business card and template for future additional sales people.
The credit card should have an eye catching design but look real. I have seen some that have similar logos to ZENO or CoinPortal too. However,it must have a smart chip design in it too. Make sure it has a black fake magnetic strip and other characteristics of an actual modern credit card.
This may be printed on paper and blank plastic cards.

Most the information will be on the back but the name will be on front with the logo, phone number.

Must Have Info:
Leonard Halvey
President

2741 Millbrook Rd, Bldg 418
Fairport, NY 14592
252-555-0187
leo@tallowmerchant.net
Updates

Phone number is 716 area code not 347! my bad

also, please add website address www.tallowmerchant.net
Thanks,

LH

Industry/Entity Type

Credit Card

Requirements
Must have
• My Logo, smart chip, fake magnetic strip

```html
<!DOCTYPE html>
<html lang="en">
<head>
<meta charset="utf-8">
<title>Tallow Merchant – Business Card</title>
<link href="https://fonts.googleapis.com/css2?family=Share+Tech+Mono&family=Roboto+Condensed:wght@400;700&display=swap" rel="stylesheet">
<style>
  :root {
    --page-bg: #e9e6e1;
    --card-black: #151816;
    --card-edge: #262a27;
    --brand-green: #3a9a2a;
    --map-green: #6aa51f;
    --map-yellow: #e6d21a;
    --emboss: #e9ecea;
    --emboss-shade: #8d928f;
    --label: #b9bdba;
    --chip-light: #f4d680;
    --chip-dark: #b98a2c;
  }
  * { margin: 0; padding: 0; box-sizing: border-box; }
  html, body { width: 1200px; height: 900px; overflow: hidden; }
  body {
    background: var(--page-bg);
    position: relative;
    font-family: "Roboto Condensed", sans-serif;
  }
  .card {
    position: absolute;
    left: 120px; top: 148px;
    width: 960px; height: 605px;
    border-radius: 36px;
    background: linear-gradient(160deg, var(--card-edge), var(--card-black) 45%);
    box-shadow: 0 24px 50px rgba(0,0,0,.35);
    overflow: hidden;
  }
  .brand {
    position: absolute;
    left: 52px; top: 44px;
    display: flex; align-items: center; gap: 14px;
  }
  .brand-mark {
    width: 26px; height: 26px;
    background: var(--brand-green);
  }
  .brand-name {
    color: var(--brand-green);
    font-weight: 700;
    font-size: 38px;
    line-height: .95;
    letter-spacing: 1px;
    text-transform: uppercase;
  }
  .pointer { position: absolute; left: 40px; top: 140px; }
  .chip { position: absolute; left: 128px; top: 140px; }
  .world-map {
    position: absolute;
    left: 400px; top: 110px;
    width: 520px; height: 360px;
    border-radius: 40% 45% 35% 50%;
    background: linear-gradient(100deg, var(--map-green) 0%, #9bb81c 40%, var(--map-yellow) 70%, #c9b414 100%);
    opacity: .85;
  }
  .embossed {
    position: absolute;
    font-family: "Share Tech Mono", monospace;
    color: var(--emboss);
    text-shadow: 1px 1px 0 var(--emboss-shade), -1px -1px 0 #ffffff;
    text-transform: uppercase;
  }
  .card-number { left: 88px; top: 262px; font-size: 64px; letter-spacing: 6px; word-spacing: 22px; }
  .holder-name { left: 88px; top: 360px; font-size: 34px; letter-spacing: 3px; }
  .holder-title { left: 134px; top: 400px; font-size: 34px; letter-spacing: 3px; }
  .validity { position: absolute; top: 400px; }
  .validity-from { left: 488px; }
  .validity-to { left: 700px; }
  .validity-label {
    display: block;
    color: var(--label);
    font-size: 14px;
    letter-spacing: 1px;
    text-transform: uppercase;
    width: 90px;
    line-height: 1.1;
  }
  .validity-date { position: static; font-size: 34px; margin-top: 6px; display: block; }
</style>
</head>
<body>
  <div class="card">
    <div class="world-map" role="img" aria-label="Dotted world map in green fading to yellow"></div>

    <div class="brand">
      <span class="brand-mark"></span>
      <span class="brand-name">Tallow<br>Merchant</span>
    </div>

    <svg class="pointer" width="80" height="70" viewBox="0 0 80 70" aria-hidden="true">
      <defs>
        <linearGradient id="pointerFill" x1="0" x2="1">
          <stop offset="0" stop-color="#f4ee2a"/>
          <stop offset="1" stop-color="#8fc21c"/>
        </linearGradient>
      </defs>
      <polygon points="0,35 80,0 80,70" fill="url(#pointerFill)"/>
    </svg>

    <svg class="chip" width="120" height="96" viewBox="0 0 120 96" aria-hidden="true">
      <defs>
        <linearGradient id="chipFill" x1="0" y1="0" x2="1" y2="1">
          <stop offset="0" stop-color="var(--chip-light)"/>
          <stop offset=".5" stop-color="#e2b54d"/>
          <stop offset="1" stop-color="var(--chip-dark)"/>
        </linearGradient>
      </defs>
      <rect x="1" y="1" width="118" height="94" rx="16" fill="url(#chipFill)" stroke="#8a6420" stroke-width="2"/>
      <g fill="none" stroke="#8a6420" stroke-width="2">
        <rect x="40" y="28" width="40" height="40" rx="8"/>
        <line x1="0" y1="30" x2="40" y2="30"/>
        <line x1="0" y1="66" x2="40" y2="66"/>
        <line x1="80" y1="30" x2="120" y2="30"/>
        <line x1="80" y1="66" x2="120" y2="66"/>
        <line x1="60" y1="0" x2="60" y2="28"/>
        <line x1="60" y1="68" x2="60" y2="96"/>
      </g>
    </svg>

    <div class="embossed card-number">1234 5678 9101 1213</div>
    <div class="embossed holder-name">Leonard Halvey</div>
    <div class="embossed holder-title">(President)</div>

    <div class="validity validity-from">
      <span class="validity-label">Valid first day of</span>
      <span class="embossed validity-date">01/13</span>
    </div>
    <div class="validity validity-to">
      <span class="validity-label">To last day of</span>
      <span class="embossed validity-date">01/14</span>
    </div>
  </div>
</body>
</html>
```